Brochure to attract insurance agents to outsource their bookkeeping

I need a brochure to handout at trade shows. Company name is Broker Office Ledger & Records. We go by BOLR. We provide bookkeeping services. I have attached the current brochure, which is a few years old, stale and outdated (not created on Pixmundo). I have also attached our graphic identity manual which show fonts/colors as well as our logo in 3 styles

Target Market(s)

Insurance Agents needing bookkeeping services

Industry/Entity Type

Accounting

Other font styles liked:
• See the graphic id manual

Colors
00AB8E
00BBA5
67D7C9
C6EFE9
E9F9F6

Requirements
Must have
• Services noted (see current brochure), contact info, reference to Vantrel Core

```html
<!DOCTYPE html>
<html lang="en">
<head>
<meta charset="utf-8">
<title>BOLR Trifold Brochure</title>
<link href="https://fonts.googleapis.com/css2?family=Signika:wght@400;600;700&family=Roboto:wght@300;400;700&display=swap" rel="stylesheet">
<style>
:root{
  --teal:#00AB8E; --teal-2:#00BBA5; --teal-3:#67D7C9; --teal-4:#C6EFE9; --teal-5:#E9F9F6;
  --ink:#2b2b2b; --muted:#555; --grey:#e4e6e6; --stage:#f4f5f5;
}
*{box-sizing:border-box;margin:0;padding:0}
html,body{width:1200px;height:1200px;overflow:hidden;background:var(--stage)}
body{font-family:"Roboto",sans-serif;color:var(--ink);display:flex;flex-direction:column;align-items:center;justify-content:center;gap:16px}
.spread{width:828px;height:580px;display:flex;box-shadow:0 6px 14px rgba(0,0,0,.18);background:#fff}
.panel{width:276px;height:580px;position:relative;overflow:hidden;display:flex;flex-direction:column}
.footer{position:absolute;left:0;right:0;bottom:0;height:22px;background:var(--teal);color:#fff;font-size:10px;display:flex;align-items:center;justify-content:center;letter-spacing:.3px}
.heading{font-family:"Signika",sans-serif;font-weight:700;line-height:1.12}

/* Services panel */
.services-head{height:128px;position:relative}
.services-head .title{position:absolute;left:118px;top:30px;color:var(--teal);font-size:24px}
.services-head .icon{position:absolute;left:54px;top:36px}
.corner{position:absolute}
.service-row{display:flex;height:58px}
.service-row .ico{width:90px;background:var(--grey);display:flex;align-items:center;justify-content:center}
.service-row .label{flex:1;display:flex;align-items:center;padding-left:12px;font-size:13px;line-height:1.2}
.service-row.on .label{background:var(--teal);color:#fff}
.service-row.off .label{background:#fff;border-left:1px solid #ddd}

/* About panel */
.about-top{background:#fff;height:128px;position:relative;padding:28px 0 0 22px}
.about-top .what{font-size:24px;color:#4a4a4a;position:relative}
.brand-word{font-family:"Signika",sans-serif;font-weight:700;color:var(--teal);font-size:46px;line-height:1;margin-top:2px;position:relative}
.about-intro{background:var(--teal-3);padding:10px 22px;font-size:10px;line-height:1.35;color:#234;height:86px}
.target{position:absolute;right:8px;top:72px;width:86px;height:86px}
.mission{flex:1;position:relative;padding:16px 16px 30px 18px;color:#fff}
.mission .bg{position:absolute;inset:0;background:linear-gradient(160deg,#7fb9ad,#5f9d92 60%,#6fa99c)}
.mission .content{position:relative}
.mission h3{font-size:22px;display:flex;gap:10px;align-items:baseline}
.mission p{font-size:9.6px;line-height:1.55;margin-top:12px}
.mission b{font-weight:700}

/* Cover panel */
.cover-top{height:360px;position:relative;background:linear-gradient(150deg,#4fc0ad,#2eae98)}
.cover-top .strip{position:absolute;top:0;left:0;right:0;height:30px;background:var(--teal-3)}
.cover-top h1{position:absolute;left:24px;top:64px;color:#fff;font-size:30px}
.cover-art{position:absolute;left:44px;top:220px;width:196px;height:100px;background:rgba(255,255,255,.18);border-radius:4px}
.cover-bottom{flex:1;position:relative;background:#fff}
.cover-bottom .logo{position:absolute;left:34px;top:58px}
.logo-word{font-family:"Signika",sans-serif;font-weight:700;font-size:50px;color:var(--teal);line-height:1}
.logo-sub{font-family:"Signika",sans-serif;font-weight:700;font-size:14px;color:var(--teal);line-height:1.15;margin-top:4px;width:200px}

/* Staff panel */
.staff-top{height:170px;position:relative}
.staff-top .title{position:absolute;left:130px;top:72px;color:#fff;font-size:26px;white-space:nowrap}
.staff-member{position:absolute;display:flex;gap:8px;align-items:flex-start}
.photo{width:76px;height:108px;background:linear-gradient(#c9cfcf,#8f9797)}
.staff-text{text-align:right;font-size:11px}
.staff-text .name{font-weight:700}
.staff-text .role{color:var(--teal);font-size:9.5px;margin-top:2px}
.staff-note{position:absolute;left:0;right:0;bottom:0;height:46px;background:var(--teal);color:#fff;font-size:8.5px;padding:9px 18px;line-height:1.5}

/* Why panel */
.why{padding:18px 20px 0 22px;background:linear-gradient(180deg,#fff,var(--teal-5))}
.why .mini{font-family:"Signika",sans-serif;font-weight:700;color:var(--teal);font-size:18px;text-align:center}
.why h2{color:var(--teal);font-size:23px;margin-top:26px}
.why-list{list-style:none;margin-top:30px}
.why-list li{display:flex;align-items:center;height:62px;font-size:12.5px;line-height:1.25}
.why-list .ico{width:56px;flex:none;display:flex;justify-content:center;border-right:1px solid #cfd;margin-right:12px;height:44px;align-items:center}
.more{position:absolute;left:0;right:0;bottom:0;height:130px;background:var(--teal);color:#fff;padding:38px 22px 0}
.more .heading{font-size:24px}
.more .url{font-size:10px;font-weight:700;margin-top:20px}

/* Fees panel */
.fees-head{background:var(--teal);height:118px;color:#fff;padding:26px 24px;position:relative}
.fees-head .heading{font-size:24px}
.fees-body{flex:1;background:linear-gradient(160deg,#e9f6f3,#b9e2da);padding:50px 18px 0}
.fees-body p{font-size:10.5px;line-height:1.55;color:#333}
.fee-table{margin-top:18px;border:4px solid #fff;width:100%;border-collapse:separate;border-spacing:4px 0;background:#fff}
.fee-table th{background:var(--teal);color:#fff;font-size:10.5px;font-weight:700;padding:6px 2px;line-height:1.25}
.fee-table td{background:var(--teal-4);font-size:10.5px;padding:5px 16px;text-align:left}
.fee-table tr:nth-child(2) td{padding-top:12px}
.fee-table tr:last-child td{padding-bottom:12px}
.phone{display:flex;gap:6px;align-items:center}
</style>
</head>
<body>

<section class="spread">
  <div class="panel services">
    <div class="services-head">
      <svg class="corner" style="left:0;top:0" width="80" height="100"><polygon points="0,0 70,0 0,90" fill="var(--teal)"/></svg>
      <svg class="corner" style="left:218px;top:0" width="60" height="60"><polygon points="0,0 58,0 58,55" fill="var(--teal-4)"/></svg>
      <svg class="icon" width="44" height="44" viewBox="0 0 44 44" fill="none" stroke="var(--teal)" stroke-width="2.4" stroke-linecap="round"><path d="M36 22a14 14 0 1 1-6-11.5"/><path d="M14 22l6 6 12-13"/><path d="M30 6l2 5-5 1"/></svg>
      <div class="title heading">Service<br>Available</div>
      <svg style="position:absolute;left:92px;top:94px" width="130" height="12"><path d="M2 9 C40 2 70 10 128 4" stroke="var(--teal)" stroke-width="1.6" fill="none"/></svg>
    </div>
    <div class="service-row on"><div class="ico"><svg width="40" height="28" viewBox="0 0 40 28" fill="none" stroke="var(--teal)" stroke-width="1.6"><rect x="2" y="8" width="28" height="16" rx="2"/><circle cx="16" cy="16" r="4"/><path d="M30 12h8M30 20h8"/></svg></div><div class="label">Reconcile &amp; Pay Agency<br>Bill Premiums</div></div>
    <div class="service-row off"><div class="ico"><svg width="30" height="34" viewBox="0 0 30 34" fill="none" stroke="var(--teal)" stroke-width="1.6"><path d="M4 2h16l6 6v24H4z"/><path d="M8 12h12M8 17h12M8 22h8"/><circle cx="21" cy="25" r="4"/></svg></div><div class="label">Record Direct Bill<br>Commission</div></div>
    <div class="service-row on"><div class="ico"><svg width="32" height="36" viewBox="0 0 32 36" fill="none" stroke="var(--teal)" stroke-width="1.6"><rect x="3" y="4" width="20" height="28" rx="2"/><path d="M7 12l2 2 3-3M7 20l2 2 3-3M14 13h6M14 21h6"/><circle cx="25" cy="26" r="5"/></svg></div><div class="label">Prepare &amp; Interpret<br>Financial Statements</div></div>
    <div class="service-row off"><div class="ico"><svg width="36" height="32" viewBox="0 0 36 32" fill="none" stroke="var(--teal)" stroke-width="1.6"><path d="M3 20l8-8 6 3 6-5 10 8-10 8-6-4-6 5z"/><circle cx="18" cy="6" r="4"/></svg></div><div class="label">Reconcile General<br>Ledger Accounts</div></div>
    <div class="service-row on"><div class="ico"><svg width="34" height="34" viewBox="0 0 34 34" fill="none" stroke="var(--teal)" stroke-width="1.6"><rect x="5" y="3" width="22" height="28" rx="2"/><path d="M9 9h14M9 14h14"/><rect x="4" y="18" width="24" height="7" transform="rotate(-15 16 21)"/></svg></div><div class="label">Reconcile Customer<br>Accounts Receivable</div></div>
    <div class="service-row off"><div class="ico"><svg width="28" height="34" viewBox="0 0 28 34" fill="none" stroke="var(--teal)" stroke-width="1.6"><rect x="3" y="2" width="22" height="30" rx="2"/><path d="M7 8h10M7 14h14M7 19h14M7 24h14"/></svg></div><div class="label">Pay Vendor Invoices</div></div>
    <div class="service-row on"><div class="ico"><svg width="36" height="30" viewBox="0 0 36 30" fill="none" stroke="var(--teal)" stroke-width="1.6"><path d="M3 10l12-7 12 7v14H3z"/><path d="M3 10l12 8 12-8"/><circle cx="28" cy="22" r="6"/></svg></div><div class="label">Process Payroll</div></div>
    <div class="footer">www.bolrledger.com</div>
  </div>

  <div class="panel about">
    <div class="about-top">
      <svg style="position:absolute;right:0;top:0" width="120" height="128"><polygon points="120,0 120,128 0,128" fill="var(--teal)"/><polygon points="90,0 120,0 120,30" fill="var(--teal-4)"/></svg>
      <div class="what heading">What is</div>
      <div class="brand-word">BOLR</div>
    </div>
    <svg class="target" viewBox="0 0 86 86" fill="none" stroke="#fff" stroke-width="2.4"><circle cx="40" cy="46" r="22"/><circle cx="40" cy="46" r="14"/><circle cx="40" cy="46" r="6"/><path d="M40 46l26-26M60 18l8-2-2 8"/></svg>
    <div class="about-intro">BOLR is a professional Accounting/Bookkeeping firm located in Connecticut dedicated exclusively to Independent Insurance Agencies.</div>
    <div class="mission">
      <div class="bg" role="img" aria-label="Faded photo of hands working over financial papers"></div>
      <div class="content">
        <h3 class="heading"><span>BOLR</span><span>Mission :</span></h3>
        <p>BOLR's mission is to provide independent insurance agencies a resource to have their accounting and bookkeeping performed accurately, timely and cost effectively. BOLR's 35 member staff is <b>led by Marta Vell.</b> Marta worked in Independent Insurance Agencies for several years before forming BOLR in 2011. <b>Her experience includes accounting, operational management, and client service.</b> She earned a bachelor's degree in accounting from Eastbrook State University and a master's degree in business administration from Harlow University. <b>Marta is an adjunct accounting professor at Northfield Community College. She serves her community as President of the local Civic League.</b></p>
      </div>
    </div>
    <div class="footer">www.bolrledger.com</div>
  </div>

  <div class="panel cover">
    <div class="cover-top">
      <div class="strip"></div>
      <h1 class="heading">Need Help with<br>Vantrel Core<br>Accounting ?</h1>
      <svg style="position:absolute;left:22px;top:178px" width="130" height="12"><path d="M2 9 C40 2 70 10 128 4" stroke="#fff" stroke-width="1.6" fill="none"/></svg>
      <div class="cover-art" role="img" aria-label="Line illustration of calculators and financial reports"></div>
    </div>
    <div class="cover-bottom">
      <svg style="position:absolute;right:0;top:0" width="150" height="90"><polygon points="0,0 150,0 150,90" fill="var(--teal-4)"/></svg>
      <div class="logo">
        <div class="logo-word">BOLR</div>
        <div class="logo-sub">Broker Office Ledger &amp; Records</div>
      </div>
    </div>
    <div class="footer">www.bolrledger.com</div>
  </div>
</section>

<section class="spread">
  <div class="panel staff">
    <div class="staff-top">
      <svg style="position:absolute;left:0;top:0" width="276" height="260"><polygon points="0,0 276,0 276,118 0,250" fill="var(--teal)"/><polygon points="0,0 60,0 0,60" fill="var(--teal-3)"/></svg>
      <svg style="position:absolute;left:118px;top:14px" width="44" height="40" viewBox="0 0 44 40" fill="none" stroke="#fff" stroke-width="2"><circle cx="22" cy="12" r="6"/><circle cx="10" cy="15" r="4"/><circle cx="34" cy="15" r="4"/><path d="M12 34c0-8 5-12 10-12s10 4 10 12M2 32c0-6 3-9 8-9M42 32c0-6-3-9-8-9"/></svg>
      <div class="title heading">Our Staff!</div>
      <svg style="position:absolute;left:18px;top:96px" width="40" height="40" viewBox="0 0 40 40" fill="none" stroke="#fff" stroke-width="2.4"><circle cx="20" cy="20" r="17"/><path d="M12 20l6 6 11-12"/></svg>
    </div>
    <div class="staff-member" style="right:8px;top:160px"><div class="staff-text" style="margin-top:52px"><div class="name">Owen Marrick</div><div class="role">Director of Accounting</div></div><div class="photo" role="img" aria-label="Portrait photo of Owen Marrick"></div></div>
    <div class="staff-member" style="left:12px;top:276px"><div class="photo" role="img" aria-label="Portrait photo of Lena Forsby"></div><div class="staff-text" style="text-align:left;margin-top:46px"><div class="name">Lena Forsby</div><div class="role">Accountant</div></div></div>
    <div class="staff-member" style="right:8px;top:386px"><div class="staff-text" style="margin-top:46px"><div class="name">Colin Avery</div><div class="role">Accountant</div></div><div class="photo" role="img" aria-label="Portrait photo of Colin Avery"></div></div>
    <svg style="position:absolute;left:12px;top:504px" width="70" height="16"><circle cx="8" cy="8" r="6" fill="none" stroke="var(--teal)" stroke-width="1.4"/><path d="M8 5v6M5 8h6" stroke="var(--teal)" stroke-width="1.4"/><circle cx="26" cy="8" r="3.5" fill="var(--teal)"/><circle cx="38" cy="8" r="3.5" fill="var(--teal)"/><circle cx="50" cy="8" r="3.5" fill="var(--teal)"/></svg>
    <div class="staff-note">For a complete list of BOLR staff and their profiles,<br>please visit <b>www.bolrledger.com</b></div>
  </div>

  <div class="panel why">
    <div class="mini">BOLR</div>
    <h2 class="heading">Why Outsourcing to<br>BOLR works?</h2>
    <svg style="position:absolute;left:22px;top:134px" width="110" height="10"><path d="M2 8 C40 2 70 8 108 3" stroke="var(--teal)" stroke-width="1.6" fill="none"/></svg>
    <ul class="why-list">
      <li><span class="ico"><svg width="34" height="32" viewBox="0 0 34 32" fill="none" stroke="var(--teal)" stroke-width="1.6"><path d="M4 16h24v6H4zM6 22h24v6H6zM17 2l12 5-12 5-12-5z"/></svg></span>Our Staff is Educated in Accounting &amp; Trained in Vantrel Core</li>
      <li><span class="ico"><svg width="34" height="34" viewBox="0 0 34 34" fill="none" stroke="var(--teal)" stroke-width="1.8"><circle cx="17" cy="17" r="15"/><circle cx="17" cy="17" r="10"/><path d="M12 17l4 4 7-8"/></svg></span>Our Work Goes through a Quality Control Process</li>
      <li><span class="ico"><svg width="34" height="34" viewBox="0 0 34 34" fill="none" stroke="var(--teal)" stroke-width="2.4"><path d="M6 17a11 11 0 1 0 4-8.5"/><path d="M4 5v7h7"/><circle cx="17" cy="17" r="3" fill="var(--teal)"/></svg></span>We always have a Backup</li>
      <li><span class="ico"><svg width="32" height="36" viewBox="0 0 32 36" fill="none" stroke="var(--teal)" stroke-width="1.6"><path d="M3 3h14l5 5v20H3z"/><path d="M7 12h10M7 17h8"/><path d="M22 18l7 3v5c0 4-3 7-7 8-4-1-7-4-7-8v-5z" fill="var(--teal)"/></svg></span>We Implement Controls for Data Security</li>
    </ul>
    <svg style="position:absolute;right:0;bottom:130px" width="90" height="80"><polygon points="90,0 90,80 0,80" fill="var(--teal-3)"/></svg>
    <div class="more">
      <div class="heading">For more<br>information</div>
      <div class="url">www.bolrledger.com</div>
    </div>
  </div>

  <div class="panel fees">
    <div class="fees-head">
      <div class="heading">How the BOLR FEES<br>are Structured ?</div>
      <svg style="position:absolute;left:40px;top:118px" width="180" height="30"><polygon points="0,0 60,0 30,26" fill="var(--teal-4)"/><polygon points="50,0 110,0 80,26" fill="var(--teal-4)"/><polygon points="100,0 160,0 130,26" fill="var(--teal-4)"/></svg>
    </div>
    <div class="fees-body">
      <p>Fees are a flat monthly rate based on annual policy commission revenue. The table below lists sample rates for our full-service offerings at different revenue velomoues for an Agency with a typical mix of business and complexity. Fees assume compliance with our standard operating workflows</p>
      <table class="fee-table">
        <tr><th>Annual<br>Commision<br>Revenue</th><th>Monthly<br>Service<br>Fee</th></tr>
        <tr><td>&lt;$300.000</td><td>$600</td></tr>
        <tr><td>$700.000</td><td>$1.400</td></tr>
        <tr><td>$1.000.000</td><td>$2000</td></tr>
        <tr><td>$1.500.000</td><td>$2.500</td></tr>
        <tr><td>$2.000.000</td><td>$3.000</td></tr>
        <tr><td>$2.500.000</td><td>$3.500</td></tr>
        <tr><td>$3.000.000</td><td>$4.500</td></tr>
      </table>
    </div>
    <div class="footer"><span class="phone"><svg width="11" height="11" viewBox="0 0 12 12"><circle cx="6" cy="6" r="6" fill="#fff"/><path d="M4 3l1 2-1 1c.5 1 1 1.5 2 2l1-1 2 1-1 1.5C5.5 9 3 6.5 3 4z" fill="var(--teal)"/></svg>555.014.72</span></div>
  </div>
</section>

</body>
</html>
```